Nanny Share Ecommerce Website for Finding Childcare and Parents who need Childcare BrightPramHub.net

Our company needs an ecommerce website (BrightPramHub.net) for a US subscription based service strictly for nanny sharing that connects families and caregivers. The website would allow families to connect with one another as well as to search for nannies. The service would be searchable for other families by location (by radius or zip code), children demographic (age range/gender/special needs), days of week or times, after school care, school closure days (holidays), etc. The service would also be searchable for nannies based on gender, provider age range, years experience, language, hourly rate, transportation available, certification (CPR first aid), education etc. The search fields would be searchable and sortable and allow to connect with the provider (after paying subscription fee). The service would be similar to tendlyfolk.net in that it would allow for families and caregivers to post photos as well as a short bio of the themselves. There would also be a feedback/star rating mechanism to rate caregivers who have performed work for families (viewable to public). The service would be free for nannies to post their bios and only a subscription based service for families to connect with other families or with caregivers (able to view bio but need service to connect). There will be a short bio on the benefits of nanny sharing (reduced cost, increased flexibility for parents, reduced illness, increased socialization with other children vs. sole nanny), as well as Q&A section with best practices.

Target Market(s)

Families, Nannies

Industry/Entity Type

Childcare

Logo Text

Bright Pram Hub

Coding

Coded - Design and coding required

Number of Pages Required

5+ page

Requirements
Must have
• Searchable (need to be able to search for families as well as nannies), responsive, functional, easy to use, add value to families and nannies. Needs to be able to collect payment for subscription.
Nice to have
• Optimized for mobile, SEO optimized

```html
<!DOCTYPE html>
<html lang="en">
<head>
<meta charset="utf-8">
<title>Bright Pram Hub</title>
<link href="https://fonts.googleapis.com/css2?family=Montserrat:wght@400;500;600&family=Open+Sans:wght@400;600&display=swap" rel="stylesheet">
<style>
:root{
  --green:#8cc43f;
  --blue:#16b4dc;
  --ink:#333;
  --muted:#6b6b6b;
  --line:#e2e2e2;
  --soft:#f3f4f6;
  --dark:#2b2b2b;
}
*{box-sizing:border-box;margin:0;padding:0}
html,body{width:1200px;height:2582px;overflow:hidden;background:#fff}
body{position:relative;font-family:"Open Sans",Arial,sans-serif;color:var(--ink)}
.abs{position:absolute}
.heading{font-family:"Montserrat",Arial,sans-serif}

/* header */
.site-header{left:0;top:0;width:1200px;height:98px;background:#fff;border-bottom:1px solid #eee}
.brand{left:86px;top:26px;display:flex;align-items:center;gap:12px}
.brand-dot{width:44px;height:44px;border-radius:50%;background:var(--green)}
.brand-name{font-family:"Montserrat",sans-serif;font-weight:500;font-size:26px;color:#444}
.main-nav a{position:absolute;top:41px;font-family:"Montserrat",sans-serif;font-size:12px;font-weight:500;color:#333;text-decoration:none;transform:translateX(-50%);white-space:nowrap}
.main-nav a.active{color:var(--blue)}
.search-btn{left:1066px;top:25px;width:48px;height:48px;border:2px solid var(--blue);border-radius:50%;display:flex;align-items:center;justify-content:center}

/* hero */
.hero{left:0;top:98px;width:1200px;height:492px;background:linear-gradient(90deg,#f4f2ee 0%,#efece6 40%,#e8d9cf 62%,#d9b9a8 80%,#c9a08a 100%)}
.hero-title{left:86px;font-size:34px;font-weight:500;color:var(--green);letter-spacing:.5px}
.hero-text{left:86px;width:410px;font-size:11.5px;line-height:26px;color:#555}
.btn{display:inline-flex;align-items:center;justify-content:center;font-family:"Montserrat",sans-serif;font-weight:500;color:#fff;text-transform:uppercase;text-decoration:none}
.btn-green{background:var(--green)}
.btn-blue{background:var(--blue)}
.hero .btn{position:absolute;top:295px;height:43px;font-size:13px}

/* section heads */
.section-title{left:0;width:1200px;text-align:center;font-size:24px;font-weight:500;color:#333}
.section-sub{left:0;width:1200px;text-align:center;font-size:11px;color:#777}

/* services */
.service-card{top:728px;width:246px;height:388px;border:1px solid var(--line);background:#fff;text-align:center}
.service-photo{height:188px}
.service-card h3{margin-top:20px;font-family:"Montserrat",sans-serif;font-size:15px;font-weight:500}
.service-card p{margin:14px auto 0;width:200px;font-size:11px;line-height:25px;color:#555}
.service-card .btn{margin-top:14px;width:112px;height:39px;font-size:11px}

/* reviews */
.reviews{left:0;top:1171px;width:1200px;height:368px;background:linear-gradient(90deg,#1fb4cf 0%,#4bbcb0 45%,#8ec955 100%);color:#fff;text-align:center}
.reviews h2{position:absolute;top:35px;width:100%;font-size:23px;font-weight:500}
.quote-ring{position:absolute;left:559px;top:79px;width:82px;height:82px;border:2px solid #fff;border-radius:50%;display:flex;align-items:center;justify-content:center;font-family:Georgia,serif;font-size:44px;line-height:1;padding-top:14px}
.review-text{position:absolute;left:220px;top:188px;width:760px;font-size:11px;line-height:28px}
.reviewer{position:absolute;top:291px;width:100%;font-family:"Montserrat",sans-serif;font-size:15px;font-weight:500}
.stars{position:absolute;top:316px;width:100%;font-size:14px;letter-spacing:3px}

/* benefits */
.benefit{top:1693px;width:260px;text-align:center;transform:translateX(-50%)}
.benefit-ring{width:130px;height:130px;margin:0 auto;border-radius:50%;padding:4px;background:linear-gradient(135deg,var(--blue),var(--green))}
.benefit-ring span{display:flex;width:100%;height:100%;border-radius:50%;background:#fff;align-items:center;justify-content:center}
.benefit h3{margin-top:26px;font-family:"Montserrat",sans-serif;font-size:14px;font-weight:500;line-height:26px;color:#333}

/* faq */
.faq{left:0;top:1937px;width:1200px;height:410px;background:var(--soft)}
.faq-item{width:484px;height:46px;background:#fff;border:1px solid var(--line);display:flex;align-items:center;font-family:"Montserrat",sans-serif;font-size:11.5px;color:#333}
.faq-item .q{width:46px;height:44px;display:flex;align-items:center;justify-content:center;font-size:22px;font-weight:600;color:var(--blue)}
.faq-item.open .q{background:var(--green);color:#fff}
.faq-item .label{flex:1;padding-left:12px}
.faq-item .chev{width:40px;text-align:center;color:#666;font-size:13px}
.faq-answer{left:146px;top:2116px;width:410px;font-size:11px;line-height:27px;color:#555}
.faq-answer a{color:var(--green);text-decoration:none}

/* footer */
.site-footer{left:0;top:2347px;width:1200px;height:235px;background:var(--dark)}
.social{top:33px;width:60px;height:60px;border:1px solid #888;border-radius:50%;display:flex;align-items:center;justify-content:center}
.footer-rule{left:86px;top:105px;width:1026px;height:1px;background:#444}
.footer-nav{left:0;top:129px;width:1200px;text-align:center;font-family:"Montserrat",sans-serif;font-size:11.5px;color:#fff}
.footer-nav span{margin:0 22px}
.copyright{left:0;top:172px;width:1200px;text-align:center;font-size:11px;color:#ddd}
</style>
</head>
<body>

<header class="site-header abs">
  <div class="brand abs"><span class="brand-dot"></span><span class="brand-name">Bright Pram Hub</span></div>
  <nav class="main-nav">
    <a class="active" style="left:486px">HOME</a>
    <a style="left:585px">ABOUT US</a>
    <a style="left:696px">SERVICES</a>
    <a style="left:801px">BENEFIT</a>
    <a style="left:904px">REVIEWS</a>
    <a style="left:1021px">CONTACT US</a>
  </nav>
  <div class="search-btn abs">
    <svg width="16" height="16" viewBox="0 0 16 16"><circle cx="6.5" cy="6.5" r="4.5" fill="none" stroke="#16b4dc" stroke-width="2"/><line x1="10" y1="10" x2="14" y2="14" stroke="#16b4dc" stroke-width="2.2" stroke-linecap="round"/></svg>
  </div>
</header>

<section class="hero abs" role="img" aria-label="Mother holding a laughing toddler in a bright room">
  <h1 class="hero-title heading abs" style="top:124px">BRIGHT PRAM HUB</h1>
  <p class="hero-text abs" style="top:185px">Sed ut perspiciatis unde omnis iste natus error sit voluptatem accusantium doloremque laudantium, totam rem aperiam, eaque ipsa quae ab illo inve et quasi architecto beatae vitae dicta sunt explicabo.</p>
  <a class="btn btn-green" style="left:86px;width:131px">Find Care</a>
  <a class="btn btn-blue" style="left:224px;width:191px">Search for Nanny</a>
</section>

<h2 class="section-title heading abs" style="top:629px">OUR SERVICES</h2>
<p class="section-sub abs" style="top:671px">Sed ut perspiciatis unde omnis iste natus error sit voluptatem accusantium doloremque laudantium, totam rem aperiam</p>

<article class="service-card abs" style="left:86px">
  <div class="service-photo" role="img" aria-label="Mother helping daughter draw" style="background:linear-gradient(135deg,#8a6a52,#e9d8c6)"></div>
  <h3 style="color:var(--blue)">CHILD CARE</h3>
  <p>Sed ut perspiciatis unde omnis iste nat us error sit voluptatem accusantium dol oremque laudantium, totam</p>
  <a class="btn btn-blue">Read More</a>
</article>
<article class="service-card abs" style="left:346px">
  <div class="service-photo" role="img" aria-label="Caregiver hugging a senior woman" style="background:linear-gradient(135deg,#b6c7d6,#f0ddd2)"></div>
  <h3 style="color:var(--green)">ADULT &amp; SENIOR CARE</h3>
  <p>Sed ut perspiciatis unde omnis iste nat us error sit voluptatem accusantium dol oremque laudantium, totam</p>
  <a class="btn btn-green">Read More</a>
</article>
<article class="service-card abs" style="left:606px">
  <div class="service-photo" role="img" aria-label="Woman with a golden dog" style="background:linear-gradient(135deg,#3b2c22,#c8a47e)"></div>
  <h3 style="color:var(--blue)">PET CARE</h3>
  <p>Sed ut perspiciatis unde omnis iste nat us error sit voluptatem accusantium dol oremque laudantium, totam</p>
  <a class="btn btn-blue">Read More</a>
</article>
<article class="service-card abs" style="left:866px">
  <div class="service-photo" role="img" aria-label="Children playing with toys at home" style="background:linear-gradient(135deg,#c44a4a,#e8c6a6)"></div>
  <h3 style="color:var(--green)">HOME CARE</h3>
  <p>Sed ut perspiciatis unde omnis iste nat us error sit voluptatem accusantium dol oremque laudantium, totam</p>
  <a class="btn btn-green">Read More</a>
</article>

<section class="reviews abs" role="img" aria-label="Soft portrait of a smiling mother behind the customer review">
  <h2 class="heading">CUSTOMER REVIEWS</h2>
  <div class="quote-ring">&ldquo;</div>
  <p class="review-text">Sed ut perspiciatis unde omnis iste natus error sit voluptatem accusantium doloremque laudantium, totam rem aperiam, eaque ipsa quae ab illo inventore veritatis et quasi architecto beatae vitae dicta sunt explicabo. Nemo enim ipsam voluptatem quia voluptas sit aspernatur aut odit aut fugit, sed quia consequuntur magni dolores eos qui ratione voluptatem sequi nesciunt.</p>
  <div class="reviewer">NAME : MARA ELLIS</div>
  <div class="stars">★★★★★</div>
</section>

<h2 class="section-title heading abs" style="top:1579px">OUR BENEFITS</h2>
<p class="section-sub abs" style="top:1622px">Sed ut perspiciatis unde omnis iste natus error sit voluptatem accusantium doloremque laudantium, totam rem aperiam</p>

<div class="benefit abs" style="left:210px">
  <div class="benefit-ring"><span>
    <svg width="62" height="62" viewBox="0 0 62 62" fill="none" stroke="#222" stroke-width="2.4"><circle cx="36" cy="20" r="13"/><text x="36" y="26" font-size="16" text-anchor="middle" fill="#222" stroke="none" font-family="Arial">$</text><path d="M6 42h10l10 4h12a3 3 0 0 1 0 6H26M16 56h24l16-10a3 3 0 0 0-4-5l-10 5"/><rect x="2" y="40" width="8" height="18" fill="#222"/></svg>
  </span></div>
  <h3>REDUCED COST</h3>
</div>
<div class="benefit abs" style="left:473px">
  <div class="benefit-ring"><span>
    <svg width="62" height="62" viewBox="0 0 62 62" fill="none" stroke="#222" stroke-width="2.2"><circle cx="31" cy="14" r="6"/><path d="M22 34a9 9 0 0 1 18 0"/><circle cx="13" cy="32" r="6"/><path d="M4 52a9 9 0 0 1 18 0"/><circle cx="49" cy="32" r="6"/><path d="M40 52a9 9 0 0 1 18 0"/><path d="M24 44h14"/></svg>
  </span></div>
  <h3>INCREASED FLEXIBILITY<br>FOR PARENTS</h3>
</div>
<div class="benefit abs" style="left:735px">
  <div class="benefit-ring"><span>
    <svg width="62" height="62" viewBox="0 0 62 62"><rect x="12" y="16" width="30" height="34" rx="4" fill="#222"/><path d="M18 16c0-6 18-6 18 0" fill="none" stroke="#222" stroke-width="3"/><circle cx="50" cy="24" r="3" fill="#222"/><circle cx="54" cy="34" r="2.5" fill="#222"/><circle cx="48" cy="42" r="2" fill="#222"/></svg>
  </span></div>
  <h3>REDUCED ILLNESS</h3>
</div>
<div class="benefit abs" style="left:999px">
  <div class="benefit-ring"><span>
    <svg width="62" height="62" viewBox="0 0 62 62" fill="none" stroke="#222" stroke-width="2.4"><path d="M6 10h30v20H18l-8 7v-7H6z"/><path d="M26 34v6h20l8 7v-7h4V22H42"/><circle cx="14" cy="20" r="1.5" fill="#222"/><circle cx="21" cy="20" r="1.5" fill="#222"/><circle cx="28" cy="20" r="1.5" fill="#222"/></svg>
  </span></div>
  <h3>INCREASED<br>SOCIALIZATION</h3>
</div>

<section class="faq abs">
  <h2 class="section-title heading abs" style="top:28px">OUR FAQ's</h2>
  <p class="section-sub abs" style="top:70px">Sed ut perspiciatis unde omnis iste natus error sit voluptatem accusantium doloremque laudantium, totam rem aperiam</p>
</section>
<div class="faq-item open abs" style="left:86px;top:2056px"><span class="q">Q</span><span class="label">SED UT PERSPICIATIS UNDE OMNIS ISTE..?</span><span class="chev">⌄</span></div>
<p class="faq-answer abs">Sed ut perspiciatis unde omnis iste natus error sit voluptatem accusantium doloremque laudantium, totam rem aperiam...<a>Read More</a></p>
<div class="faq-item abs" style="left:86px;top:2187px"><span class="q">Q</span><span class="label">SED UT PERSPICIATIS UNDE OMNIS ISTE..?</span><span class="chev">›</span></div>
<div class="faq-item abs" style="left:86px;top:2247px"><span class="q">Q</span><span class="label">SED UT PERSPICIATIS UNDE OMNIS ISTE..?</span><span class="chev">›</span></div>
<div class="faq-item abs" style="left:628px;top:2056px"><span class="q">Q</span><span class="label">SED UT PERSPICIATIS UNDE OMNIS ISTE..?</span><span class="chev">›</span></div>
<div class="faq-item abs" style="left:628px;top:2119px"><span class="q">Q</span><span class="label">SED UT PERSPICIATIS UNDE OMNIS ISTE..?</span><span class="chev">›</span></div>
<div class="faq-item abs" style="left:628px;top:2183px"><span class="q">Q</span><span class="label">SED UT PERSPICIATIS UNDE OMNIS ISTE..?</span><span class="chev">›</span></div>
<div class="faq-item abs" style="left:628px;top:2247px"><span class="q">Q</span><span class="label">SED UT PERSPICIATIS UNDE OMNIS ISTE..?</span><span class="chev">›</span></div>

<footer class="site-footer abs">
  <span class="social abs" style="left:390px" aria-label="Share">
    <svg width="18" height="18" viewBox="0 0 18 18" fill="none" stroke="#fff" stroke-width="1.6"><circle cx="4" cy="9" r="2.4"/><circle cx="14" cy="3.5" r="2.4"/><circle cx="14" cy="14.5" r="2.4"/><path d="M6 8l6-3.5M6 10l6 3.5"/></svg>
  </span>
  <span class="social abs" style="left:462px" aria-label="Chat">
    <svg width="18" height="16" viewBox="0 0 18 16" fill="none" stroke="#fff" stroke-width="1.6"><path d="M1.5 1.5h15v10H7l-4 3.5v-3.5H1.5z"/></svg>
  </span>
  <span class="social abs" style="left:533px" aria-label="Website">
    <svg width="18" height="18" viewBox="0 0 18 18" fill="none" stroke="#fff" stroke-width="1.5"><circle cx="9" cy="9" r="7.5"/><ellipse cx="9" cy="9" rx="3.2" ry="7.5"/><path d="M1.5 9h15"/></svg>
  </span>
  <span class="social abs" style="left:605px" aria-label="Link">
    <svg width="18" height="18" viewBox="0 0 18 18" fill="none" stroke="#fff" stroke-width="1.6" stroke-linecap="round"><path d="M7.5 10.5l3-3"/><path d="M8 5l1.5-1.5a3 3 0 0 1 4.5 4.5L12.5 9.5"/><path d="M10 13l-1.5 1.5a3 3 0 0 1-4.5-4.5L5.5 8.5"/></svg>
  </span>
  <span class="social abs" style="left:676px" aria-label="Phone">
    <svg width="16" height="16" viewBox="0 0 16 16" fill="none" stroke="#fff" stroke-width="1.6" stroke-linejoin="round"><path d="M3 1.5h3l1.2 3.5-2 1.2a9 9 0 0 0 4.6 4.6l1.2-2 3.5 1.2v3A1.5 1.5 0 0 1 13 14.5 11.5 11.5 0 0 1 1.5 3 1.5 1.5 0 0 1 3 1.5z"/></svg>
  </span>
  <span class="social abs" style="left:748px" aria-label="Email">
    <svg width="18" height="14" viewBox="0 0 18 14" fill="none" stroke="#fff" stroke-width="1.6"><rect x="1" y="1" width="16" height="12" rx="1"/><path d="M1 2l8 6 8-6"/></svg>
  </span>
  <div class="footer-rule abs"></div>
  <div class="footer-nav abs">HOME<span>|</span>ABOUT US<span>|</span>SERVICES<span>|</span>BENEFIT<span>|</span>REVIEWS<span>|</span>CONTACT US</div>
  <div class="copyright abs">© Copyrights 2018 Bright Pram Hub.All Rights Reserved.</div>
</footer>

</body>
</html>
```